Business Card Design

Hi I need a business card designed, we already have the business name logo artwork and would like some concept ideas for the Bus Card layout.
On the back of the card i want to include the products and services that we offer.
We are a Plastics Sheeting manufacture based in Perth Australia.

                                       

We need a BC design for a company called Tarvo Plastics based in Perth Australia.

We supply from DIY to Trade & Industrial  Engineering Markets.

We specialise in:

·         Cut to size panels  (all shapes and sizes)

·         Plastics fabrication & Welding

·         Custom Designs

·         Plastic Repairs

·         PVC Pipe Slotting & PVC Pipe Threading

·         Supplier of all types of engineering plastics and profiles.

Including:           Acrylic / Clarvene

                               Polycarbonate / Dorvil

                               Prismatic Light Diffuser

                               Vantrib

                               HDPE / UHMWPE

                               PVC / PVC Foam

                               Nylon

                               HIPS

```html
<!DOCTYPE html>
<html lang="en">
<head>
<meta charset="utf-8">
<title>Tarvo Plastics – Business Card</title>
<link rel="stylesheet" href="https://fonts.googleapis.com/css2?family=Open+Sans:wght@400;600;700;800&display=swap">
<style>
  :root {
    --bg: #e6e6ea;
    --navy: #0f2a5c;
    --navy-band: #0d2454;
    --sky: #2f8fd0;
    --orange: #e8792a;
    --green: #4a8f3a;
    --white: #ffffff;
    --ink: #2f2f33;
    --shadow: rgba(0,0,0,0.18);
  }
  * { box-sizing: border-box; margin: 0; padding: 0; }
  html, body { width: 1200px; height: 987px; overflow: hidden; }
  body {
    background: var(--bg);
    font-family: "Open Sans", Arial, sans-serif;
    display: flex; flex-direction: column; align-items: center; justify-content: center;
    gap: 44px;
  }
  .card {
    position: relative; width: 700px; height: 428px;
    border-radius: 26px; overflow: hidden;
    box-shadow: 0 10px 28px var(--shadow);
  }
  .brand-name {
    font-weight: 800; color: var(--navy); letter-spacing: -0.5px; line-height: 1;
    display: flex; align-items: center; gap: 14px;
  }
  .brand-mark { width: 22px; height: 22px; background: var(--navy); }

  /* Front */
  .card-front { background: var(--white); }
  .card-front .band { position: absolute; inset: 0; }
  .card-front .brand-name { position: absolute; top: 56px; left: 190px; font-size: 60px; }
  .contact { position: absolute; top: 168px; left: 250px; color: var(--ink); font-size: 17px; line-height: 1.55; }
  .contact .person { font-size: 22px; font-weight: 700; color: var(--navy); margin-bottom: 6px; }
  .contact .person .title { color: var(--orange); font-weight: 400; }
  .contact .row { display: flex; gap: 18px; align-items: center; }
  .contact .item { display: inline-flex; align-items: center; gap: 6px; }
  .icon { width: 15px; height: 15px; fill: var(--orange); }
  .legal { position: absolute; left: 28px; bottom: 22px; color: var(--white); font-size: 15px; }

  /* Back */
  .card-back { background: var(--green); color: var(--white); }
  .card-back .brand-name { position: absolute; top: 34px; right: 34px; font-size: 54px; }
  .tagline {
    position: absolute; top: 104px; right: 34px; text-align: right;
    color: var(--navy); font-weight: 700; font-size: 16px; line-height: 1.35;
  }
  .offer { position: absolute; top: 168px; left: 34px; right: 34px; display: flex; }
  .offer h2 { font-size: 21px; font-weight: 800; margin-bottom: 6px; }
  .offer ul { list-style: none; font-size: 15.5px; line-height: 1.42; }
  .offer li::before { content: "•"; margin-right: 6px; }
  .services { width: 360px; padding-right: 20px; }
  .divider { width: 1px; background: rgba(255,255,255,0.55); margin: 8px 24px 14px 0; }
  .materials { flex: 1; }
  .materials .pair { display: flex; gap: 16px; }
</style>
</head>
<body>

<section class="card card-front" aria-label="Business card front">
  <svg class="band" viewBox="0 0 700 428" preserveAspectRatio="none" aria-hidden="true">
    <path d="M0,196 C130,318 360,392 700,412" fill="none" stroke="var(--sky)" stroke-width="7"/>
    <path d="M0,214 C120,330 350,404 700,428 L0,428 Z" fill="var(--navy-band)"/>
  </svg>
  <div class="brand-name"><span class="brand-mark"></span>Tarvo Plastics</div>
  <div class="contact">
    <div class="person">Your Name, <span class="title">Title</span></div>
    <div class="row">
      <span class="item"><svg class="icon" viewBox="0 0 16 16"><path d="M3 1h3l1.5 4-2 1.3a9 9 0 0 0 4.2 4.2L11 8.5l4 1.5v3a2 2 0 0 1-2 2A12 12 0 0 1 1 3a2 2 0 0 1 2-2z"/></svg>08 9471 3058</span>
      <span class="item"><svg class="icon" viewBox="0 0 16 16"><rect x="4" y="0.5" width="8" height="15" rx="1.5"/><rect x="5.5" y="2.5" width="5" height="8" fill="#fff"/></svg>0400 555 812</span>
    </div>
    <div class="row">
      <span class="item"><svg class="icon" viewBox="0 0 16 16"><rect x="2" y="6" width="12" height="8" rx="1"/><rect x="4" y="2" width="8" height="5"/></svg>08 9471 3059</span>
      <span class="item"><svg class="icon" viewBox="0 0 16 16"><rect x="1" y="3" width="14" height="10" rx="1"/><path d="M1.5 3.5 8 9l6.5-5.5" stroke="#fff" stroke-width="1.5" fill="none"/></svg>sales@tarvoplastics.com.au</span>
    </div>
    <div>Unit 4/18 Halden Way Kelmscott WA 6111</div>
    <div>PO Box 2284 Kelmscott DC WA 6991</div>
  </div>
  <div class="legal">Kellbrook Holdings Pty Ltd T/A Tarvo Plastics ABN: TBA</div>
</section>

<section class="card card-back" aria-label="Business card back">
  <div class="brand-name"><span class="brand-mark"></span>Tarvo Plastics</div>
  <p class="tagline">The Products And Services That We Offer<br>Are Supplied From DIY To Trade &amp; Industrial Engineering Markets</p>
  <div class="offer">
    <div class="services">
      <h2>We specialise in:</h2>
      <ul>
        <li>Cut to size panels (all shapes and sizes)</li>
        <li>Plastics fabrication &amp; Welding</li>
        <li>Custom Designs</li>
        <li>Plastic Repairs</li>
        <li>PVC Pipe Slotting &amp; PVC Pipe Threading</li>
        <li>Supplier of all types of engineering plastics and profiles</li>
      </ul>
    </div>
    <div class="divider"></div>
    <div class="materials">
      <h2>Including:</h2>
      <ul>
        <li>Acrylic / Clarvene</li>
        <li>Polycarbonate / Dorvil</li>
        <li>Prismatic Light Diffuser</li>
        <li class="pair"><span>Vantrib</span><span>• HDPE / UHMWPE</span></li>
        <li>PVC / PVC Foam</li>
        <li class="pair"><span>Nylon</span><span>• HIPS</span></li>
      </ul>
    </div>
  </div>
</section>

</body>
</html>
```